Walk Beside The River

Business Card design

Target Market(s)

People who require support in the commnity

Industry/Entity Type

Mental Health Support

Contact Information for Business Card

Mental Health Support Rosalind Tavener walkbesidetheriver@mailcove.com.au 0481 637 092 PO Box 926 Wattlebrook QLD 4573

Colors
6B429C
8869AF
B7A5CE
E3DAEB
F3F0F8

Requirements
Must have
• Logo & details listed above
Should not have
• No red or orange

```html
<!DOCTYPE html>
<html lang="en">
<head>
<meta charset="utf-8">
<title>Walk Beside The River — Business Card</title>
<link href="https://fonts.googleapis.com/css2?family=Lato:wght@400;700;900&display=swap" rel="stylesheet">
<style>
  :root {
    --stage: #2b2b2e;
    --violet-deep: #7b35c4;
    --violet-mid: #8a47cc;
    --violet-soft: #9a5fd2;
    --cream: #fbf6d8;
    --sun: #f7ea1f;
    --white: #ffffff;
  }
  * { box-sizing: border-box; margin: 0; padding: 0; }
  html, body { width: 1200px; height: 875px; overflow: hidden; }
  body {
    background: var(--stage);
    font-family: "Lato", sans-serif;
    display: flex;
    align-items: center;
    justify-content: center;
    gap: 40px;
  }
  .card {
    position: relative;
    width: 540px;
    height: 310px;
    border-radius: 22px;
    overflow: hidden;
    background:
      radial-gradient(ellipse 60% 50% at 75% 20%, rgba(170,110,220,0.55), transparent 70%),
      radial-gradient(ellipse 55% 45% at 20% 80%, rgba(165,105,215,0.5), transparent 70%),
      radial-gradient(ellipse 40% 40% at 40% 35%, rgba(110,40,180,0.35), transparent 70%),
      linear-gradient(135deg, var(--violet-mid), var(--violet-deep) 50%, var(--violet-soft));
    box-shadow: 0 18px 40px rgba(0,0,0,0.45);
  }
  /* Front */
  .card--front {
    display: flex;
    flex-direction: column;
    align-items: center;
    justify-content: center;
    gap: 18px;
  }
  .brand-dot {
    width: 64px;
    height: 64px;
    border-radius: 50%;
    background: var(--sun);
  }
  .brand-name {
    color: var(--cream);
    font-weight: 400;
    font-size: 19px;
    letter-spacing: 0.28em;
    text-transform: uppercase;
  }
  /* Back */
  .card--back {
    display: flex;
    align-items: center;
    padding: 0 30px 0 36px;
    color: var(--white);
  }
  .identity { flex: none; text-align: right; padding-right: 18px; margin-top: 40px; }
  .identity__name {
    font-weight: 900;
    font-size: 25px;
    letter-spacing: -0.01em;
    text-transform: uppercase;
    line-height: 1;
  }
  .identity__role {
    font-weight: 400;
    font-size: 15px;
    margin-top: 4px;
  }
  .divider {
    flex: none;
    width: 1px;
    height: 62px;
    background: var(--white);
    margin-top: 40px;
  }
  .contacts {
    list-style: none;
    padding-left: 16px;
    margin-top: 40px;
    display: flex;
    flex-direction: column;
    gap: 4px;
  }
  .contacts li { display: flex; align-items: center; gap: 7px; font-size: 11px; white-space: nowrap; }
  .contacts .contacts__phone { font-size: 17px; font-weight: 700; }
  .contacts svg { width: 11px; height: 11px; fill: var(--white); flex: none; }
</style>
</head>
<body>
  <section class="card card--front" aria-label="Card front">
    <span class="brand-dot"></span>
    <span class="brand-name">Walk Beside The River</span>
  </section>

  <section class="card card--back" aria-label="Card back">
    <div class="identity">
      <p class="identity__name">Rosalind Tavener</p>
      <p class="identity__role">Mental Health Support</p>
    </div>
    <span class="divider"></span>
    <ul class="contacts">
      <li class="contacts__phone">
        <svg viewBox="0 0 24 24" aria-hidden="true"><path d="M6.6 10.8a15.1 15.1 0 0 0 6.6 6.6l2.2-2.2a1 1 0 0 1 1-.25 11.4 11.4 0 0 0 3.6.57 1 1 0 0 1 1 1V20a1 1 0 0 1-1 1A17 17 0 0 1 3 4a1 1 0 0 1 1-1h3.5a1 1 0 0 1 1 1c0 1.25.2 2.45.57 3.57a1 1 0 0 1-.25 1z"/></svg>
        0481 637 092
      </li>
      <li>
        <svg viewBox="0 0 24 24" aria-hidden="true"><path d="M2 5h20v14H2z M2 5l10 8 10-8" fill="none" stroke="#fff" stroke-width="2"/></svg>
        walkbesidetheriver@mailcove.com.au
      </li>
      <li>
        <svg viewBox="0 0 24 24" aria-hidden="true"><path d="M12 2a7 7 0 0 0-7 7c0 5.2 7 13 7 13s7-7.8 7-13a7 7 0 0 0-7-7zm0 9.5A2.5 2.5 0 1 1 12 6.5a2.5 2.5 0 0 1 0 5z"/></svg>
        PO Box 926 Wattlebrook QLD 4573
      </li>
    </ul>
  </section>
</body>
</html>
```